U.S. Popcorn company needs business cards

We are a popcorn company that manufactures popcorn and sells it to grocery stores worldwide. Our theme is "Americana" and our logo is U.S. route 66 which is the most famous highway in the U.S.

We would like the design to be simple and to use both sides. On the back side we would like to see just the logo and website. The front would be normal details

Target Market(s)

Wholesalers, grocers and distributors

Industry/Entity Type

Manufacture

Contact Information for Business Card

Business name: Prairie Lantern Popcorn
Phone: +1 555 308 4726
Email: Dale@prairielanternpopcorn.com
website: www.prairielanternpopcorn.com
Tag Line: "POPular for a reason"
Name: Dale Whitcombe
Title: Founder/President

Requirements
Must have
• Either this design should be fun or clean and simple. I will let you show me your thougths.
Nice to have
• Anything that ties in the real Hwy Route 66.
• Colors might need to be red, white and blue incorporated.
Should not have
• Not be too busy.

```html
<!DOCTYPE html>
<html lang="en">
<head>
<meta charset="utf-8">
<title>Prairie Lantern Popcorn – Business Cards</title>
<link rel="stylesheet" href="https://fonts.googleapis.com/css2?family=Open+Sans:wght@400;600;700&display=swap">
<style>
  :root {
    --backdrop: #e9e6e1;
    --card-black: #0d0d0e;
    --card-black-soft: #1a1a1c;
    --route-red: #e0202e;
    --route-blue: #0f2a6e;
    --ink-white: #ffffff;
    --ink-grey: #d9d9d9;
  }
  * { box-sizing: border-box; margin: 0; padding: 0; }
  html, body {
    width: 1200px;
    height: 900px;
    overflow: hidden;
    background: var(--backdrop);
    font-family: "Open Sans", Arial, sans-serif;
  }
  .sheet {
    position: relative;
    width: 1200px;
    height: 900px;
  }
  .card {
    position: absolute;
    width: 525px;
    height: 300px;
    border-radius: 4px;
    overflow: hidden;
    background: radial-gradient(ellipse at 40% 30%, var(--card-black-soft), var(--card-black) 75%);
    box-shadow: 0 12px 28px rgba(0,0,0,0.25);
  }
  .card--back { left: 337px; top: 110px; }
  .card--front { left: 337px; top: 480px; }

  .brand-name {
    color: var(--ink-white);
    font-weight: 700;
    text-transform: uppercase;
    letter-spacing: 0.04em;
    text-align: center;
    line-height: 1.2;
  }
  .card--back .brand-name {
    position: absolute;
    left: 0; right: 0; top: 50%;
    transform: translateY(-50%);
    font-size: 26px;
  }
  .card--front .brand-name {
    position: absolute;
    right: 28px; top: 34px;
    width: 150px;
    font-size: 16px;
  }

  .person {
    position: absolute;
    left: 40px; top: 58px;
  }
  .person__name {
    color: var(--route-red);
    font-weight: 700;
    font-size: 17px;
    text-transform: uppercase;
    letter-spacing: 0.01em;
  }
  .person__title {
    color: var(--ink-white);
    font-size: 13px;
    margin-top: 2px;
  }

  .contacts {
    position: absolute;
    left: 40px; top: 128px;
    list-style: none;
  }
  .contacts li {
    display: flex;
    align-items: center;
    gap: 10px;
    color: var(--ink-grey);
    font-size: 13px;
    line-height: 22px;
  }
  .contacts svg { width: 11px; height: 11px; fill: var(--route-red); flex: none; }

  .swoosh {
    position: absolute;
    left: 0; top: 0;
    width: 525px; height: 300px;
  }
  .swoosh .band-blue { fill: var(--route-blue); }
  .swoosh .band-red { fill: var(--route-red); }

  .tagline {
    position: absolute;
    left: 40px; bottom: 26px;
    color: var(--ink-white);
    font-size: 20px;
  }
</style>
</head>
<body>
<main class="sheet">

  <section class="card card--back" aria-label="Card back">
    <p class="brand-name">Prairie Lantern Popcorn</p>
  </section>

  <section class="card card--front" aria-label="Card front">
    <svg class="swoosh" viewBox="0 0 525 300" aria-hidden="true">
      <path class="band-red" d="M250 196 C360 190 470 150 525 78 L525 98 C450 165 360 192 250 196 Z"/>
      <path class="band-blue" d="M0 222 C160 190 390 215 525 104 L525 300 L0 300 Z"/>
    </svg>

    <p class="brand-name">Prairie Lantern Popcorn</p>

    <div class="person">
      <p class="person__name">Dale Whitcombe</p>
      <p class="person__title">Founder/President</p>
    </div>

    <ul class="contacts">
      <li>
        <svg viewBox="0 0 12 12" aria-hidden="true"><path d="M1 3c0-1 1-2 2-2h6c1 0 2 1 2 2v1H8V3H4v1H1zM2 5h8l1 6H1z"/></svg>
        +1 555 308 4726
      </li>
      <li>
        <svg viewBox="0 0 12 12" aria-hidden="true"><path d="M0 2h12v8H0z M1 3l5 4 5-4" stroke="#0d0d0e" stroke-width="1"/></svg>
        Dale@prairielanternpopcorn.com
      </li>
      <li>
        <svg viewBox="0 0 12 12" aria-hidden="true"><circle cx="6" cy="6" r="6"/></svg>
        www.prairielanternpopcorn.com
      </li>
    </ul>

    <p class="tagline">Popular for a reason</p>
  </section>

</main>
</body>
</html>
```